Fresh, modern, fun business card for pediatric dental practice

Need a business card for fresh, modern, fun pediatric dental practice

Clean look that matches our website's font and colors

We prefer the look of curved corners on business cards

Target Market(s)

parents (mothers) of young children, professionals, mid-high class

Industry/Entity Type

Dental

Contact Information for Business Card

Maplebrook Pediatric Dentistry
482 Quarry Lane
Suite 517
Fernwood, PA 17890
717.555.0193
www.maplebrookkidsdental.example

Mei-Ran Tsai, DMD
Corinne Walbeck, DMD
(we are working on our email address, but we would like that on the card as well)

Font styles to use
Sans Serif

Requirements
Must have
• All info; we would also like to make cards for individual staff members
• colors from our website and color palatte, attatched
• use same font and design as website for branding
Nice to have
• clean, simple card that has a pop of color
• we would like to see a few designs with our tag line "where smiles get brighter"
• we are not sure if we want to have it on there or not
• we would like to see a few designs incorporating the ribbon graphic on our website where the word WELCOME is

```html
<!DOCTYPE html>
<html lang="en">
<head>
<meta charset="utf-8">
<title>Maplebrook Pediatric Dentistry – Business Card</title>
<link rel="stylesheet" href="https://fonts.googleapis.com/css2?family=Montserrat:wght@500&family=Open+Sans:wght@400;600;700&display=swap">
<style>
  :root {
    --backdrop: #2b2522;
    --card: #0d0d0d;
    --accent: #f2b416;
    --ink: #f2f2f2;
    --silver: #cfd0d2;
    --divider: #3a3a3a;
  }
  * { margin: 0; padding: 0; box-sizing: border-box; }
  html, body { width: 1200px; height: 900px; overflow: hidden; }
  body {
    background: var(--backdrop);
    font-family: "Open Sans", Arial, sans-serif;
    position: relative;
  }
  .card {
    position: absolute;
    top: 302px;
    width: 520px;
    height: 297px;
    background: var(--card);
    border-radius: 16px;
  }
  .card--front { left: 50px; }
  .card--back { left: 630px; display: flex; align-items: center; justify-content: center; }

  .front__mark {
    position: absolute;
    left: 0; top: 0;
    width: 200px; height: 100%;
    display: flex; align-items: center; justify-content: center;
  }
  .front__divider {
    position: absolute;
    left: 200px; top: 80px;
    width: 1px; height: 150px;
    background: var(--divider);
  }
  .front__info {
    position: absolute;
    left: 222px; top: 38px;
    right: 16px;
  }
  .doctors {
    font-family: "Montserrat", Arial, sans-serif;
    font-weight: 500;
    color: var(--accent);
    font-size: 17px;
    line-height: 1.15;
  }
  .doctors .degree { font-size: 11px; }
  .practice {
    margin-top: 14px;
    color: var(--accent);
    font-weight: 700;
    font-size: 13px;
  }
  .address {
    color: var(--ink);
    font-size: 12px;
    line-height: 1.5;
    margin-top: 2px;
  }
  .contacts {
    list-style: none;
    margin-top: 14px;
    color: var(--ink);
    font-size: 12px;
  }
  .contacts li { display: flex; align-items: center; gap: 9px; line-height: 1.55; white-space: nowrap; }
  .contacts svg { width: 10px; height: 10px; flex: none; }

  .brand {
    text-align: left;
    color: var(--silver);
    font-weight: 600;
    line-height: 1;
  }
  .brand__name { font-size: 50px; letter-spacing: 1px; display: flex; align-items: center; gap: 12px; }
  .brand__dot { width: 16px; height: 16px; border-radius: 50%; background: var(--silver); flex: none; }
  .brand__line { font-size: 22px; letter-spacing: 2px; margin-top: 6px; padding-left: 30px; }
</style>
</head>
<body>
  <section class="card card--front" aria-label="Business card front">
    <div class="front__mark">
      <svg width="120" height="120" viewBox="0 0 120 120" aria-hidden="true">
        <circle cx="60" cy="60" r="44" fill="none" stroke="var(--accent)" stroke-width="6"/>
      </svg>
    </div>
    <div class="front__divider"></div>
    <div class="front__info">
      <p class="doctors">Mei-Ran Tsai, <span class="degree">DMD</span><br>Corinne Walbeck, <span class="degree">DMD</span></p>
      <p class="practice">Maplebrook Pediatric Dentistry</p>
      <p class="address">482 Quarry Lane Suite<br>517 Fernwood, PA 17890</p>
      <ul class="contacts">
        <li><svg viewBox="0 0 10 10"><path d="M2 1 L4 1 L4.6 3 L3.4 3.8 Q4.4 5.8 6.2 6.6 L7 5.4 L9 6 L9 8 Q5 9.5 1 1.8 Z" fill="var(--accent)"/></svg>717.555.0193</li>
        <li><svg viewBox="0 0 10 10"><rect x="0.5" y="2" width="9" height="6.5" fill="var(--accent)"/><path d="M0.8 2.3 L5 5.6 L9.2 2.3" fill="none" stroke="var(--card)" stroke-width="0.9"/></svg>mei-ran@maplebrookkidsdental.example</li>
        <li><svg viewBox="0 0 10 10"><rect x="0.5" y="2" width="9" height="6.5" fill="var(--accent)"/><path d="M0.8 2.3 L5 5.6 L9.2 2.3" fill="none" stroke="var(--card)" stroke-width="0.9"/></svg>corinne@maplebrookkidsdental.example</li>
        <li><svg viewBox="0 0 10 10"><circle cx="5" cy="5" r="4.5" fill="var(--accent)"/><path d="M0.5 5 H9.5 M5 0.5 Q2.5 5 5 9.5 M5 0.5 Q7.5 5 5 9.5" fill="none" stroke="var(--card)" stroke-width="0.7"/></svg>www.maplebrookkidsdental.example</li>
      </ul>
    </div>
  </section>

  <section class="card card--back" aria-label="Business card back">
    <div class="brand">
      <div class="brand__name"><span class="brand__dot"></span>maplebrook</div>
      <div class="brand__line">pediatric dentistry</div>
    </div>
  </section>
</body>
</html>
```